Website Design - TallyPorchHelpers.net

PLEASE CHECK WORD DOCUMENT ATTACHED FOR WEBSITE FLOW.

Target Market(s)

REAL ESTATE AGENTS ARE THE TARGET MARKET

Industry/Entity Type

Real Estate

Coding

Coded - Design and coding required

Number of Pages Required

4 page

Colors

Designer to choose colors to be used in the design.

Requirements
Must have
• WE LIKE RED LOGO ATTACHED
Nice to have
• PLEASE CHECK WORD DOCUMENT ATTACHED FOR WEBSITE FLOW.
Should not have

```html
<!DOCTYPE html>
<html lang="en">
<head>
<meta charset="utf-8">
<title>TallyPorchHelpers.net</title>
<link rel="stylesheet" href="https://fonts.googleapis.com/css2?family=Roboto+Condensed:wght@400;700&family=Roboto:wght@400;500;700&display=swap">
<style>
:root{
  --navy:#1b2f8c;
  --blue:#1f4aa6;
  --red:#c5161d;
  --red-dark:#a10f15;
  --ice:#e4ecf7;
  --ink:#222;
  --muted:#555;
  --line:#d9d9d9;
  --footer:#1d1d1d;
  --footer-bar:#141414;
  --quote:#2b2c8c;
  --white:#fff;
}
*{box-sizing:border-box;margin:0;padding:0}
html,body{width:1200px;height:4749px;overflow:hidden}
body{font-family:"Roboto",Arial,sans-serif;color:var(--ink);background:var(--white);position:relative}
.heading{font-family:"Roboto Condensed","Arial Narrow",sans-serif;font-weight:400;text-transform:uppercase;text-align:center;color:#222;font-size:36px;letter-spacing:.5px}
section,header,footer{position:relative;width:1200px}

/* header */
.site-header{height:127px}
.brand{position:absolute;left:89px;top:38px;display:flex;align-items:center;gap:12px}
.brand-mark{width:30px;height:30px;background:var(--navy)}
.brand-name{font-family:"Roboto Condensed",sans-serif;font-weight:700;font-size:26px;line-height:1;color:var(--navy);text-transform:uppercase;width:230px}
.top-phone{position:absolute;right:89px;top:28px;display:flex;align-items:center;gap:8px;font-size:15px;color:#333}
.main-nav{position:absolute;top:72px;left:525px;display:flex;font-size:16px;color:#333}
.main-nav a{color:inherit;text-decoration:none;margin-right:0}
.main-nav a:nth-child(1){margin-right:65px}
.main-nav a:nth-child(2){margin-right:52px}
.main-nav a:nth-child(3){margin-right:52px}
.main-nav a:nth-child(4){margin-right:60px}
.main-nav a:nth-child(5){margin-right:44px}

/* hero */
.hero{height:506px;background:linear-gradient(180deg,#9dbbe0 0%,#bfd3ea 28%,#6d8a5a 60%,#4f7a34 82%,#3c6326 100%)}
.hero-text{position:absolute;right:100px;top:190px;width:560px;text-align:right;color:var(--white);font-size:25px;line-height:1.45;text-shadow:0 1px 3px rgba(0,0,0,.5)}

/* choose band */
.choose{height:247px;background:var(--blue);text-align:center}
.choose .heading{color:var(--white);font-size:30px;padding-top:55px}
.choose-options{display:flex;justify-content:center;gap:22px;margin-top:40px}
.choose-options a{display:block;background:var(--white);color:#222;font-family:"Roboto Condensed",sans-serif;font-weight:700;font-size:15px;text-decoration:none;width:260px;height:52px;line-height:52px;text-transform:uppercase;box-shadow:0 2px 4px rgba(0,0,0,.25)}

/* how it works */
.how{height:560px}
.how .heading{padding-top:100px}
.steps{position:absolute;top:206px;left:89px;display:flex;gap:24px}
.step{width:323px;height:260px;text-align:center;padding-top:30px}
.step.featured{box-shadow:0 2px 12px rgba(0,0,0,.2);border:1px solid #eee}
.step-icon{width:100px;height:100px;margin:0 auto 22px;border-radius:50%;background:var(--blue);border:6px solid #dfe8f5;display:flex;align-items:center;justify-content:center}
.step p{font-size:16px;color:#444;line-height:1.4;width:240px;margin:0 auto}

/* services */
.services{height:650px}
.services-band{position:absolute;top:0;left:0;width:1200px;height:380px;background:var(--red)}
.services .heading{position:relative;color:var(--white);padding-top:65px}
.service-cards{position:absolute;top:168px;left:89px;display:flex;gap:24px}
.service-card{width:323px;height:418px;background:var(--white);box-shadow:0 2px 10px rgba(0,0,0,.22);text-align:center}
.service-photo{height:215px;background:linear-gradient(180deg,#c9d9ea,#8aa07a 60%,#5b7c3e)}
.service-card h3{font-weight:400;font-size:20px;margin:26px 0 12px}
.service-card p{font-size:14px;color:#555;line-height:1.55;width:270px;margin:0 auto}
.pill{display:inline-block;background:var(--red);color:var(--white);font-size:13px;padding:6px 22px;border-radius:16px;margin-top:14px;text-decoration:none}

/* pricing */
.pricing{height:640px}
.pricing .heading{padding-top:39px}
.plans{position:absolute;top:108px;left:82px;display:flex;gap:10px}
.plan{width:203px;height:373px;border:1px solid #ccc;box-shadow:0 1px 6px rgba(0,0,0,.2);text-align:center;background:var(--white)}
.plan-name{font-family:"Roboto Condensed",sans-serif;font-weight:700;font-size:17px;height:35px;line-height:35px}
.plan-head{height:60px;background:var(--navy);position:relative}
.plan-price{position:absolute;left:50%;top:0;transform:translateX(-50%);width:80px;height:80px;border-radius:50%;background:var(--red);border:4px solid var(--white);color:var(--white);font-family:"Roboto Condensed",sans-serif;font-weight:700;font-size:27px;line-height:72px}
.plan-custom{font-family:"Roboto Condensed",sans-serif;font-weight:700;color:var(--white);font-size:15px;line-height:1.35;padding-top:8px}
.plan ol{list-style:none;font-size:13px;color:#444;line-height:1.35;padding:45px 18px 0}
.plan.custom ol{padding-top:25px}
.plan li{margin-bottom:12px}
.plan .buy{display:block;color:var(--red);font-size:13px;margin-top:12px;text-decoration:none}

/* subscription */
.subscribe{height:707px;background:var(--ice)}
.subscribe .heading{padding-top:92px;line-height:1.45;font-size:34px}
.perks{position:absolute;top:250px;left:60px;display:flex}
.perk{width:270px;text-align:center}
.perk-icon{width:112px;height:112px;border-radius:50%;background:var(--white);border:3px solid #2a8fc7;margin:0 auto;display:flex;align-items:center;justify-content:center}
.perk h4{font-family:"Roboto Condensed",sans-serif;font-size:20px;font-weight:700;margin:26px 0 10px}
.perk p{font-size:15px;color:#444;line-height:1.5;width:230px;margin:0 auto}
.signup{position:absolute;left:540px;top:585px;width:120px;height:48px;line-height:48px;background:var(--red);color:var(--white);text-align:center;font-family:"Roboto Condensed",sans-serif;font-size:18px;text-decoration:none;box-shadow:0 2px 3px rgba(0,0,0,.3)}

/* faq */
.faq{height:712px}
.faq .heading{padding-top:100px}
.faq-list{position:absolute;top:190px;left:171px;width:858px}
.faq-item{height:90px;border:1px solid #ccc;border-left:6px solid var(--red);box-shadow:0 1px 5px rgba(0,0,0,.15);padding:18px 26px;margin-bottom:14px}
.faq-item h5{font-weight:400;font-size:17px;margin-bottom:8px}
.faq-item p{font-size:13px;color:#444}

/* testimonial */
.testimonial{height:184px;background:var(--quote);color:var(--white);text-align:center}
.quote-badge{position:absolute;left:566px;top:-34px;width:68px;height:68px;border-radius:50%;background:var(--white);display:flex;align-items:center;justify-content:center}
.testimonial p{font-size:15px;line-height:1.9;padding-top:58px;width:900px;margin:0 auto}
.testimonial cite{display:block;font-size:14px;margin-top:18px}

/* footer */
.site-footer{height:418px;background:var(--footer);color:var(--white)}
.site-footer h6{font-family:"Roboto Condensed",sans-serif;font-size:22px;font-weight:400;text-transform:uppercase;margin-bottom:22px}
.foot-col{position:absolute;top:90px}
.foot-about{left:89px;width:330px}
.foot-about p{font-size:15px;line-height:1.8;color:#ddd}
.foot-contact{left:519px}
.contact-row{display:flex;gap:12px;margin-bottom:22px}
.contact-row strong{display:block;font-size:14px;font-weight:700;text-transform:uppercase}
.contact-row span{font-size:13px;color:#ddd;line-height:1.5}
.foot-links{list-style:none;font-size:15px;line-height:2.2;color:#ddd}
.foot-about-links{left:810px}
.foot-resources{left:988px}
.copyright{position:absolute;bottom:0;left:0;width:1200px;height:72px;background:var(--footer-bar);text-align:center;line-height:72px;font-size:13px;color:#bbb}
</style>
</head>
<body>

<header class="site-header">
  <div class="brand"><span class="brand-mark"></span><span class="brand-name">Tally Porch Helpers</span></div>
  <div class="top-phone">
    <svg width="22" height="22" viewBox="0 0 24 24"><circle cx="12" cy="12" r="11" fill="none" stroke="#c5161d" stroke-width="2"/><path d="M8 6l2 3-1.5 1.5a8 8 0 004 4L14 13l3 2-1 2.5C11 17 7 13 6.5 8z" fill="#c5161d"/></svg>
    Call Or Text Us 1-555-014-0196
  </div>
  <nav class="main-nav"><a href="#">How it works</a><a href="#">Service</a><a href="#">Pricing</a><a href="#">About us</a><a href="#">Faq</a><a href="#">Contact</a></nav>
</header>

<section class="hero" role="img" aria-label="Photo of a suburban house with a lawn and a for-sale sign post">
  <p class="hero-text">Helping agents save time and money. We place signs and boost foot traffic to your open houses using proven marketing techniques.</p>
</section>

<section class="choose">
  <h2 class="heading">Choose the option below that best describes you</h2>
  <div class="choose-options">
    <a href="#">I'm a full on brokerage</a>
    <a href="#">I'm an ind. broker with a team</a>
    <a href="#">I need sign placement asap</a>
  </div>
</section>

<section class="how">
  <h2 class="heading">How it works</h2>
  <div class="steps">
    <div class="step">
      <div class="step-icon"><svg width="40" height="40" viewBox="0 0 24 24"><path d="M12 2a7 7 0 00-7 7c0 5 7 13 7 13s7-8 7-13a7 7 0 00-7-7z" fill="none" stroke="#fff" stroke-width="1.8"/><circle cx="12" cy="9" r="2.5" fill="#fff"/></svg></div>
      <p>Place signs strategically in best areas according to where the open house is located</p>
    </div>
    <div class="step featured">
      <div class="step-icon"><svg width="42" height="42" viewBox="0 0 24 24"><path d="M3 11l9-7 9 7M5 10v10h14V10" fill="none" stroke="#fff" stroke-width="1.8"/><rect x="10" y="14" width="4" height="6" fill="#fff"/></svg></div>
      <p>Pick Up the signs after the open house</p>
    </div>
    <div class="step">
      <div class="step-icon"><svg width="42" height="42" viewBox="0 0 24 24"><rect x="3" y="5" width="18" height="10" fill="none" stroke="#fff" stroke-width="1.8"/><path d="M7 15v6M17 15v6M7 10h10" stroke="#fff" stroke-width="1.8"/></svg></div>
      <p>Store custom signs for you if needed</p>
    </div>
  </div>
</section>

<section class="services">
  <div class="services-band"></div>
  <h2 class="heading">Our services</h2>
  <div class="service-cards">
    <article class="service-card">
      <div class="service-photo" role="img" aria-label="Photo of a house with a sold sign on the lawn"></div>
      <h3>Neque porro quisquam</h3>
      <p>It is a long established fact that a reader will be distracted by the readable content of a page when looking at its layout.</p>
      <a class="pill" href="#">View More</a>
    </article>
    <article class="service-card">
      <div class="service-photo" role="img" aria-label="Photo of a for-rent sign in front of a house"></div>
      <h3>Dolorem ipsum quia</h3>
      <p>It is a long established fact that a reader will be distracted by the readable content of a page when looking at its layout.</p>
      <a class="pill" href="#">View More</a>
    </article>
    <article class="service-card">
      <div class="service-photo" role="img" aria-label="Photo of a family home with a front yard"></div>
      <h3>Neque porro quisquam</h3>
      <p>It is a long established fact that a reader will be distracted by the readable content of a page when looking at its layout.</p>
      <a class="pill" href="#">View More</a>
    </article>
  </div>
</section>

<section class="pricing">
  <h2 class="heading">Pricing package</h2>
  <div class="plans">
    <div class="plan"><div class="plan-name">5 Signs</div><div class="plan-head"><div class="plan-price">$49</div></div>
      <ol><li>1. Place signs strategically in best areas according to where the open house is located</li><li>2. Pick Up the signs after the open house</li><li>3. Store custom signs for you if needed</li></ol><a class="buy" href="#">BUY NOW »</a></div>
    <div class="plan"><div class="plan-name">10 Signs</div><div class="plan-head"><div class="plan-price">$59</div></div>
      <ol><li>1. Place signs strategically in best areas according to where the open house is located</li><li>2. Pick Up the signs after the open house</li><li>3. Store custom signs for you if needed</li></ol><a class="buy" href="#">BUY NOW »</a></div>
    <div class="plan"><div class="plan-name">15 Signs</div><div class="plan-head"><div class="plan-price">$69</div></div>
      <ol><li>1. Place signs strategically in best areas according to where the open house is located</li><li>2. Pick Up the signs after the open house</li><li>3. Store custom signs for you if needed</li></ol><a class="buy" href="#">BUY NOW »</a></div>
    <div class="plan"><div class="plan-name">20 Signs</div><div class="plan-head"><div class="plan-price">$79</div></div>
      <ol><li>1. Place signs strategically in best areas according to where the open house is located</li><li>2. Pick Up the signs after the open house</li><li>3. Store custom signs for you if needed</li></ol><a class="buy" href="#">BUY NOW »</a></div>
    <div class="plan custom"><div class="plan-name">25+ Signs</div><div class="plan-head"><div class="plan-custom">Click Buy Now<br>To Create Custom Pkg</div></div>
      <ol><li>1. Place signs strategically in best areas according to where the open house is located</li><li>2. Pick Up the signs after the open house</li><li>3. Store custom signs for you if needed</li></ol><a class="buy" href="#">BUY NOW »</a></div>
  </div>
</section>

<section class="subscribe">
  <h2 class="heading">Sign up for a subscription and get these<br>marketing services for free</h2>
  <div class="perks">
    <div class="perk">
      <div class="perk-icon"><svg width="46" height="46" viewBox="0 0 24 24"><path d="M3 4h18v12H9l-5 4v-4H3z" fill="none" stroke="#2a8fc7" stroke-width="1.5"/><circle cx="8" cy="10" r="1" fill="#2a8fc7"/><circle cx="12" cy="10" r="1" fill="#2a8fc7"/><circle cx="16" cy="10" r="1" fill="#2a8fc7"/></svg></div>
      <h4>SMS</h4><p>Send sms blast to your neighborhood informing them your home is for sale and if they know anyone looking to send them over</p>
    </div>
    <div class="perk">
      <div class="perk-icon"><svg width="48" height="48" viewBox="0 0 24 24"><rect x="2" y="5" width="20" height="14" fill="none" stroke="#2a8fc7" stroke-width="1.5"/><path d="M2 5l10 8 10-8" fill="none" stroke="#2a8fc7" stroke-width="1.5"/></svg></div>
      <h4>EMAIL</h4><p>Email blast to your neighborhood informing them your home is for sale and if they know anyone looking to send them over</p>
    </div>
    <div class="perk">
      <div class="perk-icon"><svg width="44" height="44" viewBox="0 0 24 24"><rect x="3" y="3" width="18" height="18" rx="2" fill="none" stroke="#2a8fc7" stroke-width="1.5"/></svg></div>
      <h4>FB AD</h4><p>Newsfeed ads to people in your open house area</p>
    </div>
    <div class="perk">
      <div class="perk-icon"><svg width="46" height="46" viewBox="0 0 24 24"><path d="M13 3h8v8L11 21l-8-8z" fill="none" stroke="#2a8fc7" stroke-width="1.5"/><circle cx="17" cy="7" r="1.5" fill="#2a8fc7"/></svg></div>
      <h4>VB</h4><p>VB blast to your neighborhood informing them your home is for sale and if they know anyone looking to send them over</p>
    </div>
  </div>
  <a class="signup" href="#">SIGN UP</a>
</section>

<section class="faq">
  <h2 class="heading">FAQ</h2>
  <div class="faq-list">
    <div class="faq-item"><h5>Q- Why choose Tally Porch?</h5><p>A- It is a long established fact that a reader will be distracted by the readable content of a page .</p></div>
    <div class="faq-item"><h5>Q- quisquam est qui dolorem ipsum quia dolor sit amet?</h5><p>A- The point of using Lorem Ipsum is that it has a more-or-less normal distribution of letters, as opposed</p></div>
    <div class="faq-item"><h5>Q- Neque porro quisquam est qui dolorem ipsum quia dolor sit amet?</h5><p>A- Lorem Ipsum as their default model text, and a search for 'lorem ipsum' will uncover many web sites.</p></div>
    <div class="faq-item"><h5>Q- Porro quisquam est qui dolorem ipsum quia dolor sit amet, consectetur?</h5><p>A- Various versions have evolved over the years, sometimes by accident, sometimes on purpose</p></div>
  </div>
</section>

<section class="testimonial">
  <div class="quote-badge"><svg width="30" height="24" viewBox="0 0 30 24"><path d="M2 24V13C2 6 6 2 12 1v5c-3 1-4 3-4 6h4v12zM17 24V13c0-7 4-11 10-12v5c-3 1-4 3-4 6h4v12z" fill="#2b2c8c"/></svg></div>
  <p>The point of using Lorem Ipsum is that it has a more-or-less normal distribution of letters, as opposed to using 'Content here, content here', making it look like readable English Many desktop publishing packages and web page editors now</p>
  <cite>- Neque porro quisquam</cite>
</section>

<footer class="site-footer">
  <div class="foot-col foot-about">
    <h6>About us</h6>
    <p>Helping agents leverage their time and skills to increase production at an affordable price with impeccable support.</p>
  </div>
  <div class="foot-col foot-contact">
    <h6>Contact us</h6>
    <div class="contact-row">
      <svg width="22" height="26" viewBox="0 0 24 24"><path d="M12 2a7 7 0 00-7 7c0 5 7 13 7 13s7-8 7-13a7 7 0 00-7-7z" fill="none" stroke="#fff" stroke-width="1.6"/><circle cx="12" cy="9" r="2.5" fill="none" stroke="#fff" stroke-width="1.6"/></svg>
      <div><strong>Address</strong><span>48 Birch Lane, Suite B<br>Larkton, NC 27000</span></div>
    </div>
    <div class="contact-row">
      <svg width="22" height="22" viewBox="0 0 24 24"><path d="M6 3l3 4-2 2a11 11 0 008 8l2-2 4 3-2 3C10 21 3 14 3 5z" fill="none" stroke="#fff" stroke-width="1.6"/></svg>
      <div><strong>Phone number</strong><span>(555) 010-8700</span></div>
    </div>
  </div>
  <div class="foot-col foot-about-links">
    <h6>About</h6>
    <ul class="foot-links"><li>Home</li><li>About Us</li><li>Services</li><li>Training</li></ul>
  </div>
  <div class="foot-col foot-resources">
    <h6>Resources</h6>
    <ul class="foot-links"><li>Support</li><li>Why Us</li><li>Testimonials</li><li>FAQ</li></ul>
  </div>
  <div class="copyright">© 2018 Company Name  All right reserved</div>
</footer>

</body>
</html>
```